Transform Your Giving

I need a tri-fold brochure that will fit in a standard number 10 business envelope. Meadowlark and Allied Services is a charitable nonprofit. The goal of this brochure is to stimulate people into thinking about other ways to make a donation. The design should communicate the essential information on donation options, create a sense of professional integrity, be graphically sharp, easy to read and laid out in a way that doesn't make the material appear crowded.

```html
<!DOCTYPE html>
<html lang="en">
<head>
<meta charset="utf-8">
<title>Transform Your Giving – Tri-fold Brochure</title>
<link rel="stylesheet" href="https://fonts.googleapis.com/css2?family=Montserrat:ital,wght@0,300;0,400;0,500;0,600;0,700;0,800;1,400&display=swap">
<style>
:root{
  --navy:#2b2a6e;
  --navy-deep:#232262;
  --green:#4cb848;
  --green-dark:#3ea43a;
  --paper:#ffffff;
  --panel:#ededed;
  --panel-alt:#e4e4e4;
  --stage:#c8bfbc;
  --ink:#3b3b4a;
}
*{box-sizing:border-box;margin:0;padding:0}
html,body{width:1200px;height:1200px;overflow:hidden;background:var(--stage)}
body{font-family:"Montserrat",Arial,sans-serif;color:var(--ink)}
.canvas{position:relative;width:1200px;height:1200px;background:var(--stage);overflow:hidden}
.sheet{position:absolute;left:274px;width:660px;height:514px;overflow:hidden}
.sheet--outside{top:71px;background:var(--paper)}
.sheet--inside{top:621px;background:var(--panel)}
.abs{position:absolute}
.layer{position:absolute;left:0;top:0;width:660px;height:514px}
.icons{position:absolute;width:0;height:0}

/* outside – left panel */
.impact-title{left:0;width:217px;top:20px;text-align:center;font-weight:800;font-size:15.5px;line-height:19px;color:var(--navy);letter-spacing:.2px}
.impact-title span{color:var(--green)}
.impact-copy{left:22px;width:173px;top:66px;text-align:center;font-size:7.5px;line-height:9.8px;color:var(--ink)}
.checklist{left:44px;top:155px;width:132px;list-style:none}
.checklist li{height:16px;margin-bottom:5.2px;border:1px solid var(--green);display:flex;align-items:center;justify-content:center;gap:4px;font-size:8.6px;color:var(--ink)}
.checklist svg{width:8px;height:8px;color:var(--green)}

/* logo stand-in */
.brand{font-weight:800;font-size:17px;color:var(--navy);letter-spacing:.3px;display:flex;align-items:center;gap:5px}
.brand i{display:block;width:9px;height:9px;border-radius:50%;background:var(--green)}
.brand-sub{font-weight:700;font-size:3.6px;color:var(--navy);letter-spacing:.2px;text-align:center;margin-top:2px}
.brand-wrap{width:120px;text-align:center;display:flex;flex-direction:column;align-items:center}

/* outside – middle panel */
.invite{left:240px;width:176px;top:72px;text-align:center;font-size:8.2px;line-height:10px;font-weight:500;color:var(--navy)}
.quote-hex{left:313px;top:205px;width:36px;height:41px}
.quote{left:225px;width:205px;top:251px;text-align:center;font-style:italic;font-size:8.4px;line-height:10.6px;color:#e9e8f3}
.quote cite{display:block;font-style:normal;font-size:7.4px;font-weight:600;color:var(--green);margin-top:2px}
.will{left:220px;width:215px;top:296px;text-align:center;color:#fff}
.will-lead{font-size:7.6px;font-weight:500}
.will-link{font-size:12.4px;font-weight:800;color:var(--green);line-height:15px}
.will-note{font-size:7.6px;color:#e3e2f0}
.will-note strong{display:block;font-weight:700;font-size:8.4px;color:#fff}
.contact-btn{left:279px;top:356px;width:97px;height:17px;border-radius:9px;background:var(--green);color:#fff;font-weight:800;font-size:10px;text-align:center;line-height:17px;letter-spacing:.3px}
.more{left:220px;width:215px;top:380px;text-align:center;color:#fff}
.more h3{font-size:10.6px;font-weight:800;line-height:12px}
.more p{font-size:7.6px;line-height:9.6px;color:#e3e2f0}
.rule{height:1px;background:rgba(255,255,255,.5)}
.contact-details{left:240px;top:429px;width:195px;display:flex;gap:10px;font-size:5.9px;line-height:7.9px;color:#fff}
.contact-details .col{display:flex;gap:3px}
.contact-details svg{width:6px;height:7px;color:var(--green);flex:none;margin-top:1px}
.follow{left:220px;width:215px;top:458px;text-align:center;font-size:7.6px;color:#fff;font-weight:500}
.disclaimer{left:240px;width:175px;top:476px;text-align:center;font-size:3.5px;line-height:4.6px;color:#c9c8df}

/* outside – right panel */
.hex-label{font-weight:700;fill:#fff;text-anchor:middle}
.transform{left:438px;width:222px;top:394px;text-align:center;color:#fff;font-weight:800;font-size:18.5px;line-height:20px;letter-spacing:.6px}
.transform span{display:block;color:var(--green);font-size:24.5px;line-height:28px;letter-spacing:.4px}
.slogan{left:451px;width:190px;top:442px;height:22px;border-top:1px solid rgba(255,255,255,.55);border-bottom:1px solid rgba(255,255,255,.55);display:flex;align-items:center;justify-content:center;gap:8px;color:#fff;font-weight:700;font-size:10.6px}
.slogan span{display:flex;align-items:center;gap:3px}
.slogan svg{width:12px;height:12px;color:var(--green)}
.discover{left:438px;width:222px;top:472px;text-align:center;color:#fff;font-weight:700;font-size:7.6px;line-height:10px}

/* inside */
.ways-badge{left:17px;top:20px;width:189px;height:65px}
.ways-num{left:35px;top:22px;font-weight:800;font-size:56px;line-height:60px;color:var(--green)}
.ways-text{left:74px;top:29px;font-weight:800;font-size:15.4px;line-height:15.6px;color:#fff;letter-spacing:.2px}
.way-hex{width:55px;height:62px}
.way-title{font-weight:700;font-size:11.8px;line-height:14.8px;color:var(--navy)}
.way-sub{font-weight:700;font-size:6.6px;line-height:8.8px;color:var(--green)}
.way-body{font-size:6.6px;line-height:8.8px;color:var(--ink)}
.how{height:13px;padding:0 7px;border-radius:7px;background:var(--green);color:#fff;font-size:7.4px;font-weight:500;line-height:13px;white-space:nowrap}
.how::after{content:"";position:absolute;left:7px;bottom:-3px;border-left:3px solid transparent;border-right:3px solid transparent;border-top:4px solid var(--green)}
.tick-item{display:flex;gap:6px}
.tick-item svg{width:9px;height:9px;flex:none;color:var(--green);margin-top:1px}
</style>
</head>
<body>
<div class="canvas">

<svg class="icons" aria-hidden="true">
  <defs>
    <symbol id="i-tick" viewBox="0 0 20 20"><circle cx="10" cy="10" r="8.2" fill="none" stroke="currentColor" stroke-width="1.6" stroke-dasharray="44 8"/><path d="M6 10.2l3 3 6-6.6" fill="none" stroke="currentColor" stroke-width="1.8" stroke-linecap="round" stroke-linejoin="round"/></symbol>
    <symbol id="i-stocks" viewBox="0 0 40 40"><g fill="none" stroke="currentColor" stroke-width="1.6" stroke-linejoin="round"><rect x="5" y="26" width="5" height="10"/><rect x="13" y="20" width="5" height="16"/><rect x="21" y="23" width="5" height="13"/><rect x="29" y="14" width="5" height="22"/><polyline points="6,17 14,10 22,14 32,5"/><path d="M3 36h34"/></g><g fill="currentColor"><circle cx="6" cy="17" r="1.8"/><circle cx="14" cy="10" r="1.8"/><circle cx="22" cy="14" r="1.8"/><circle cx="32" cy="5" r="1.8"/></g></symbol>
    <symbol id="i-bank" viewBox="0 0 40 40"><g fill="none" stroke="currentColor" stroke-width="1.6" stroke-linejoin="round"><path d="M4 14L20 5l16 9z"/><path d="M5 17h30"/><path d="M8 19v12M13 19v12M18 19v12M22 19v12M27 19v12M32 19v12"/><path d="M5 33h30M3 36h34"/><circle cx="20" cy="11" r="1.5"/></g></symbol>
    <symbol id="i-coin" viewBox="0 0 40 40"><g fill="none" stroke="currentColor" stroke-width="1.8"><circle cx="20" cy="20" r="16"/><circle cx="20" cy="20" r="11"/></g></symbol>
    <symbol id="i-gift" viewBox="0 0 40 40"><g fill="none" stroke="currentColor" stroke-width="1.6" stroke-linejoin="round"><rect x="7" y="18" width="26" height="18"/><rect x="4" y="12" width="32" height="6"/><path d="M20 12v24"/><path d="M20 12c-4-7-11-6-9-1 1 2 5 1 9 1zM20 12c4-7 11-6 9-1-1 2-5 1-9 1z"/></g></symbol>
    <symbol id="i-annuity" viewBox="0 0 40 40"><g fill="none" stroke="currentColor" stroke-width="1.6" stroke-linecap="round"><circle cx="18" cy="20" r="13"/><path d="M16 4h4M18 4v3M18 20l5-6"/><circle cx="29" cy="29" r="6.5"/><path d="M29 25.5v7M27 27.2h3.4a1.2 1.2 0 010 2.4h-2.8a1.2 1.2 0 000 2.4h3.4"/></g></symbol>
    <symbol id="i-pin" viewBox="0 0 12 14"><path d="M6 13S1.5 8 1.5 5a4.5 4.5 0 019 0C10.5 8 6 13 6 13z" fill="none" stroke="currentColor" stroke-width="1.2"/><circle cx="6" cy="5" r="1.6" fill="none" stroke="currentColor" stroke-width="1.1"/></symbol>
    <symbol id="i-phone" viewBox="0 0 12 14"><rect x="3" y="1" width="6" height="12" rx="1.2" fill="none" stroke="currentColor" stroke-width="1.1"/></symbol>
    <symbol id="i-mail" viewBox="0 0 12 14"><rect x="1.5" y="4" width="9" height="6" fill="none" stroke="currentColor" stroke-width="1"/><path d="M1.5 4l4.5 3.5L10.5 4" fill="none" stroke="currentColor" stroke-width="1"/></symbol>
    <symbol id="i-globe" viewBox="0 0 12 14"><circle cx="6" cy="7" r="4.5" fill="none" stroke="currentColor" stroke-width="1"/><path d="M1.5 7h9M6 2.5c-2.5 3-2.5 6 0 9M6 2.5c2.5 3 2.5 6 0 9" fill="none" stroke="currentColor" stroke-width=".9"/></symbol>
    <linearGradient id="g-field" x1="0" y1="0" x2="1" y2="1"><stop offset="0" stop-color="#e9efe0"/><stop offset=".45" stop-color="#9bb66a"/><stop offset="1" stop-color="#4f6f33"/></linearGradient>
    <linearGradient id="g-sunset" x1="0" y1="0" x2="1" y2="1"><stop offset="0" stop-color="#f3c46a"/><stop offset=".4" stop-color="#c8874a"/><stop offset="1" stop-color="#5b3a2a"/></linearGradient>
    <linearGradient id="g-lake" x1="0" y1="0" x2="0" y2="1"><stop offset="0" stop-color="#5c7a48"/><stop offset=".35" stop-color="#7ea2b5"/><stop offset="1" stop-color="#d9dde0"/></linearGradient>
  </defs>
</svg>

<!-- ============ OUTSIDE SPREAD ============ -->
<section class="sheet sheet--outside">
  <svg class="layer" viewBox="0 0 660 514">
    <path d="M217 99 C250 140 290 190 335 222 C400 268 490 262 552 205 C600 160 640 110 660 58 L660 514 L217 514 Z" fill="var(--navy)"/>
    <path d="M335 222 C400 268 490 262 552 205 C600 160 640 110 660 58" fill="none" stroke="var(--green)" stroke-width="9"/>
    <path d="M334 208 C360 120 420 55 500 40 C580 28 630 45 660 60 C640 110 600 160 552 205 C490 262 400 262 334 208 Z" fill="url(#g-field)" role="img" aria-label="Photo: smiling young man in a cap leaning on a garden tool in a green field"/>
    <path d="M0 266 C90 255 175 290 225 355" fill="none" stroke="var(--green)" stroke-width="9"/>
    <path d="M0 283 C85 276 165 310 214 370 L222 514 L0 514 Z" fill="url(#g-sunset)" role="img" aria-label="Photo: older couple in outdoor jackets reading a map together at sunset"/>
  </svg>

  <h2 class="abs impact-title">THE IMPACT OF<br><span>YOUR GIFT</span></h2>
  <p class="abs impact-copy">Your generosity drives our mission. With every Smart gift you’re supporting Meadowlark and Allied Services. Join our community of Smart Givers today and make an enduring impact. With Smart Giving your generosity reaches further. Begin your Smart Giving journey with us today.</p>
  <ul class="abs checklist">
    <li><svg><use href="#i-tick"/></svg>Stocks and Securities</li>
    <li><svg><use href="#i-tick"/></svg>DAFs</li>
    <li><svg><use href="#i-tick"/></svg>QCDs</li>
    <li><svg><use href="#i-tick"/></svg>Crypto</li>
    <li><svg><use href="#i-tick"/></svg>Charitable Annuity</li>
  </ul>

  <div class="abs brand-wrap" style="left:267px;top:30px">
    <div class="brand"><i></i>Meadowlark</div>
    <div class="brand-sub">MEADOWLARK AND ALLIED SERVICES, INC.</div>
  </div>
  <p class="abs invite">To learn more about Smart Giving Options and how they can benefit you and Meadowlark and Allied Services, please reach out to our team. We’re here to help you navigate these giving methods and answer any question you may have.</p>

  <svg class="abs quote-hex" viewBox="0 0 100 115"><polygon points="50,0 100,28.75 100,86.25 50,115 0,86.25 0,28.75" fill="var(--green)"/><text x="50" y="100" text-anchor="middle" font-family="Montserrat, sans-serif" font-weight="800" font-size="96" fill="#fff">“</text></svg>
  <blockquote class="abs quote">Being kind to others is a way of being good to yourself.<cite>Harriet Kessler</cite></blockquote>

  <div class="abs will">
    <p class="will-lead">If you do not have a will</p>
    <p class="will-link">go to www.EasyWillNow.com</p>
    <p class="will-note">In 20 minutes you can have a<strong>legal will – for free.</strong></p>
  </div>
  <div class="abs contact-btn">CONTACT US</div>
  <div class="abs more"><h3>Have more question?</h3><p>Please contact us at Meadowlark and<br>Allied Services</p></div>
  <div class="abs rule" style="left:234px;top:419px;width:191px"></div>
  <div class="abs contact-details">
    <div class="col"><svg><use href="#i-pin"/></svg><span>1420 Prairie View Rd.<br>Suite 2<br>Millbrook, ND 58000</span></div>
    <div class="col"><span style="display:flex;flex-direction:column;gap:1px"><svg><use href="#i-phone"/></svg><svg><use href="#i-mail"/></svg><svg><use href="#i-globe"/></svg></span><span>555-014-2200 (ext. 100)<br>info@meadowlarkallied.org<br>www.meadowlarkallied.org</span></div>
  </div>
  <p class="abs follow">Follow us</p>
  <p class="abs disclaimer">This material is for general information only and is not tax, legal or accounting advice. Meadowlark and Allied Services is not a professional fiduciary. Please consult your tax advisor or financial professional before making a decision about Smart Giving.</p>

  <div class="abs brand-wrap" style="left:426px;top:30px">
    <div class="brand"><i></i>Meadowlark</div>
    <div class="brand-sub">MEADOWLARK AND ALLIED SERVICES, INC.</div>
  </div>

  <svg class="abs" style="left:446px;top:256px;width:200px;height:124px" viewBox="0 0 200 124" font-family="Montserrat, sans-serif">
    <g transform="translate(0.5,0)">
      <polygon points="29.5,0 59,17 59,51 29.5,68 0,51 0,17" fill="var(--green)"/>
      <use href="#i-coin" x="17" y="12" width="25" height="25" color="#fff"/>
      <text class="hex-label" x="29.5" y="47" font-size="5.6">Crypto</text>
    </g>
    <g transform="translate(68.5,0)">
      <polygon points="29.5,0 59,17 59,51 29.5,68 0,51 0,17" fill="var(--green)"/>
      <use href="#i-bank" x="17" y="12" width="25" height="25" color="#fff"/>
      <text class="hex-label" x="29.5" y="47" font-size="5.6">DAF’s</text>
    </g>
    <g transform="translate(135.5,0)">
      <polygon points="29.5,0 59,17 59,51 29.5,68 0,51 0,17" fill="var(--green)"/>
      <use href="#i-stocks" x="17" y="11" width="25" height="25" color="#fff"/>
      <text class="hex-label" x="29.5" y="45" font-size="5.4">Stocks &amp;</text>
      <text class="hex-label" x="29.5" y="52" font-size="5.4">Securities</text>
    </g>
    <g transform="translate(35.5,56)">
      <polygon points="29.5,0 59,17 59,51 29.5,68 0,51 0,17" fill="var(--green)"/>
      <use href="#i-stocks" x="17" y="11" width="25" height="25" color="#fff"/>
      <text class="hex-label" x="29.5" y="45" font-size="5.4">Stocks &amp;</text>
      <text class="hex-label" x="29.5" y="52" font-size="5.4">Securities</text>
    </g>
    <g transform="translate(102.5,56)">
      <polygon points="29.5,0 59,17 59,51 29.5,68 0,51 0,17" fill="var(--green)"/>
      <use href="#i-stocks" x="17" y="11" width="25" height="25" color="#fff"/>
      <text class="hex-label" x="29.5" y="45" font-size="5.4">Stocks &amp;</text>
      <text class="hex-label" x="29.5" y="52" font-size="5.4">Securities</text>
    </g>
  </svg>

  <h1 class="abs transform">TRANSFORM<span>YOUR GIVING</span></h1>
  <div class="abs slogan"><span><svg><use href="#i-tick"/></svg>Be Strategic</span><span><svg><use href="#i-tick"/></svg>Be Smart</span></div>
  <p class="abs discover">Discover the impact of Smart Giving with<br>Meadowlark and Allied Services</p>
</section>

<!-- ============ INSIDE SPREAD ============ -->
<section class="sheet sheet--inside">
  <svg class="layer" viewBox="0 0 660 514">
    <rect x="217" y="0" width="222" height="514" fill="var(--panel-alt)"/>
    <path d="M0 0 L660 0 L660 514 L0 514 Z" fill="none"/>
    <path d="M80 0 L596 0 C545 45 480 82 410 100 C330 122 240 116 175 88 C130 68 100 38 80 0 Z" fill="url(#g-lake)" role="img" aria-label="Photo: three older men in sun hats and sunglasses fishing from a boat on a lake"/>
    <path d="M172 86 C250 125 360 128 448 104" fill="none" stroke="var(--green)" stroke-width="8"/>
    <path d="M0 0 L80 0 C60 8 30 18 0 24 Z" fill="#fff"/>
    <path d="M596 0 L660 0 L660 6 C640 4 615 2 596 0 Z" fill="#fff"/>
    <path d="M178 514 C250 470 370 462 478 514 Z" fill="var(--navy)"/>
    <path d="M170 514 C240 464 360 454 440 488" fill="none" stroke="var(--green)" stroke-width="6"/>
  </svg>

  <svg class="abs ways-badge" viewBox="0 0 189 65"><rect x="1" y="1" width="187" height="63" rx="31.5" fill="var(--navy)" stroke="#fff" stroke-width="2"/><polygon points="40,63 52,63 46,71" fill="var(--navy)"/></svg>
  <div class="abs ways-num">5</div>
  <h2 class="abs ways-text">STRATEGIC<br>AND SMART<br>WAYS</h2>

  <!-- column 1 -->
  <svg class="abs way-hex" style="left:18px;top:101px" viewBox="0 0 100 115"><polygon points="50,0 100,28.75 100,86.25 50,115 0,86.25 0,28.75" fill="var(--navy)"/><use href="#i-stocks" x="26" y="33" width="48" height="48" color="#fff"/></svg>
  <h3 class="abs way-title" style="left:81px;top:107px;width:125px">Gifts of Stocks or Appreciated Assets Strategic &amp; Smart</h3>
  <p class="abs way-sub" style="left:81px;top:156px;width:120px">Consider your long-term publicly traded stock as a way to give to your favorite charity.</p>
  <p class="abs way-body" style="left:18px;top:185px;width:187px">You can make a significantly bigger impact when you donate long-term appreciated securities, including stock, mutual funds, and bonds, directly to your favorite charity.</p>
  <div class="abs how" style="left:19px;top:224px">How Does It Work?</div>
  <p class="abs way-body" style="left:18px;top:249px;width:190px">When you donate stock to a charity, you will generally take a tax deduction for the full market value. Because you are donating stock, your contribution and tax deduction may be significantly higher than contributing the after-tax proceeds. The same benefits apply when you donate mutual funds or bonds.</p>

  <svg class="abs way-hex" style="left:18px;top:303px" viewBox="0 0 100 115"><polygon points="50,0 100,28.75 100,86.25 50,115 0,86.25 0,28.75" fill="var(--navy)"/><use href="#i-bank" x="26" y="33" width="48" height="48" color="#fff"/></svg>
  <h3 class="abs way-title" style="left:81px;top:308px;width:120px">Donor-Advised Fund (DAF) Strategic &amp; Smart</h3>
  <p class="abs way-sub" style="left:81px;top:357px;width:125px">Consider a DAF – a simple, flexible, and tax-advantageous way to give to your favorite charities.</p>
  <p class="abs way-body" style="left:18px;top:388px;width:187px">A Donor-Advised Fund (DAF), is like a charitable investment account for the sole purpose of supporting your favorite charities.</p>
  <div class="abs how" style="left:19px;top:418px">How Does It Work?</div>
  <p class="abs way-body" style="left:18px;top:441px;width:192px">You establish a DAF and contribute cash, stocks, or non-publicly traded assets, cryptocurrency, and private company stock to be eligible for an immediate tax deduction. Those funds are contributed for tax-free growth. You can recommend grants be made from your DAF to any IRS qualified public charity.</p>

  <!-- column 2 -->
  <svg class="abs way-hex" style="left:240px;top:155px" viewBox="0 0 100 115"><polygon points="50,0 100,28.75 100,86.25 50,115 0,86.25 0,28.75" fill="var(--navy)"/><use href="#i-coin" x="28" y="35" width="44" height="44" color="#fff"/></svg>
  <h3 class="abs way-title" style="left:300px;top:160px;width:125px">Cryptocurrency Strategic &amp; Smart</h3>
  <p class="abs way-sub" style="left:300px;top:193px;width:120px">Consider donating Bitcoin and other cryptocurrencies to your favorite charity.</p>
  <p class="abs way-body" style="left:240px;top:228px;width:190px">Bitcoin and other cryptocurrencies can be donated to charity just like other appreciated assets such as stocks and other business interests. Before you sell bitcoin and donate the after-tax proceeds, consider donating your bitcoin directly to a favorite charity.</p>
  <div class="abs how" style="left:241px;top:279px">How Does It Work?</div>
  <p class="abs way-body" style="left:240px;top:304px;width:180px">Many donors find it useful to open a Donor-Advised Fund (DAF). This strategy includes two significant benefits, both for you and your favorite charity.</p>
  <div class="abs way-body tick-item" style="left:240px;top:338px;width:190px"><svg><use href="#i-tick"/></svg><span>Your tax deduction will be equal to the fair market value of the donated bitcoin (as determined by a qualified appraisal).</span></div>
  <div class="abs way-body tick-item" style="left:240px;top:373px;width:190px"><svg><use href="#i-tick"/></svg><span>Your cryptocurrency donation is tax-smart because it may eliminate capital gains taxes on the value / appreciation AND your favorite charity will receive 100% of the value of the contribution.</span></div>
  <p class="abs way-body" style="left:240px;top:419px;width:190px">Often charities are not able to accept direct donations of bitcoin/crypto so using a DAF is a great way to donate these assets.</p>

  <!-- column 3 -->
  <svg class="abs way-hex" style="left:451px;top:56px" viewBox="0 0 100 115"><polygon points="50,0 100,28.75 100,86.25 50,115 0,86.25 0,28.75" fill="var(--navy)"/><use href="#i-gift" x="26" y="33" width="48" height="48" color="#fff"/></svg>
  <h3 class="abs way-title" style="left:517px;top:61px;width:135px">Qualified Charitable Distributions (QCDs) Strategic &amp; Smart</h3>
  <p class="abs way-sub" style="left:517px;top:108px;width:135px">Consider a QCD – when planning your IRA withdrawal strategy...and donate to your favorite charity.</p>
  <p class="abs way-body" style="left:450px;top:141px;width:200px">IRA owners at age 70 ½ or over can transfer dollars from their IRA to charity tax-free each year. These transfers known as Qualified Charitable Distributions (QCDs) offer eligible older Americans a great way to easily give to charity.</p>
  <div class="abs how" style="left:450px;top:191px">How Does It Work?</div>
  <p class="abs way-body" style="left:450px;top:215px;width:206px">Are you 72 and required to take a minimum distribution (RMD) from your IRA but do not need the funds? Consider a Qualified Charitable Distribution. Normally, distributions from a traditional IRA are taxable when received. With a QCD, these distributions become tax-free when paid directly from the IRA to your favorite eligible charity. An IRA owner wishing to make a QCD should contact their IRA trustee, allowing time to complete the transaction before the end of the year to receive the tax benefit.</p>

  <svg class="abs way-hex" style="left:452px;top:304px" viewBox="0 0 100 115"><polygon points="50,0 100,28.75 100,86.25 50,115 0,86.25 0,28.75" fill="var(--navy)"/><use href="#i-annuity" x="26" y="33" width="48" height="48" color="#fff"/></svg>
  <h3 class="abs way-title" style="left:523px;top:305px;width:130px">Charitable Gift Annuity Strategic &amp; Smart</h3>
  <p class="abs way-sub" style="left:523px;top:351px;width:130px">Consider establishing a Charitable Gift Annuity</p>
  <p class="abs way-body" style="left:449px;top:377px;width:200px">You make a donation to a single charity. The gift is set aside in a reserve account and invested.</p>
  <div class="abs how" style="left:450px;top:398px">How Does It Work?</div>
  <p class="abs way-body" style="left:449px;top:422px;width:207px">A charitable gift annuity is a contract between a donor and a charity. As a donor, you make a sizable gift to charity using cash, securities, or possibly other assets. This money is then invested. In return, you become eligible to take a partial tax deduction for your donation, plus you receive a fixed stream of income from the charity for the rest of your life. At the end of your life (as well as your spouse’s, if you’re giving as a couple), the charity receives the remainder of the gift.</p>
</section>

</div>
</body>
</html>
```